Modern Label for cleaning products for the brand Vorlix

We need a label design for our line of cleaning products. The label should feature our logo and an image to identify the product's intended use. I've added our logo and an image for use. This only concerns the design of the label on the front of the bottle.

Label dimensions:
Label 1 (500ml bottle with spray): width 58mm x height 115mm
Label 2: (1L bottle): width 73mm x height 140mm
The design must be consistent for both bottles which you find in the pictures.

The bottles to be labeled are white. See the attachment for a photo of the bottles.

The photo must also appear on the label to identify the product's intended use.

Product information:
Brand: Vorlix
Product: Sanitary Cleaner

This text must be placed on the label:
"Cleans, descales & freshens. followed with this text: "Ideal for quick and powerful cleaning. A ready-to-use product for everyday use."

- Mention the seperate USP's: Sanitary, Bathroom, Toilet, Wet areas

Appearance: This is a consumer product, but it must have a professional appearance. We would like to see a design that use the color blue from our logo.

Target Market(s)

Consumers who take care of their homes and want to maintain it the correct (professional) way

Font styles to use
Sans Serif

Colors
0054AA
0677BA
7BADD7
CADEEF
E8F1F8

Requirements
Must have
• USP's + use of image and logo + blend in 1 design
Nice to have
• Keep the color of the logo in the design
Should not have
• Comic sans

```html
<!DOCTYPE html>
<html lang="en">
<head>
<meta charset="utf-8">
<title>Vorlix Sanitary Cleaner – Labels</title>
<link href="https://fonts.googleapis.com/css2?family=Montserrat:wght@400;500;700&display=swap" rel="stylesheet">
<style>
  :root {
    --page: #ffffff;
    --ink: #1c1c1c;
    --outline: #222222;
    --navy: #003a74;
    --navy-deep: #00336a;
    --brand-blue: #0054aa;
    --mid-blue: #0677ba;
    --sky-blue: #0092d8;
    --badge: #00aeef;
    --white: #ffffff;
  }
  html, body {
    margin: 0;
    padding: 0;
    width: 1200px;
    height: 989px;
    overflow: hidden;
    background: var(--page);
  }
  .canvas {
    position: relative;
    width: 1200px;
    height: 989px;
    font-family: "Montserrat", sans-serif;
  }
  .label { position: absolute; display: block; }
  .label--500 { left: 160px; top: 178px; width: 341.5px; height: 677px; }
  .label--1000 { left: 599px; top: 77px; width: 431px; height: 825px; }
  .label text { font-family: "Montserrat", sans-serif; }
  .wordmark { fill: var(--ink); font-weight: 700; }
  .title { fill: var(--white); font-weight: 500; }
  .tagline { fill: var(--white); font-weight: 500; }
  .badge-text { fill: var(--white); font-weight: 500; }
  .usp { fill: var(--white); font-weight: 500; }
  .usage { fill: var(--white); font-weight: 500; }
  .volume { fill: var(--white); font-weight: 500; }
  .tick-ring { fill: none; stroke: var(--white); }
  .tick-mark { fill: none; stroke: var(--white); stroke-linecap: round; stroke-linejoin: round; }
</style>
</head>
<body>
<div class="canvas">

  <!-- 500 ml label -->
  <svg class="label label--500" viewBox="0 0 605 1200" xmlns="http://www.w3.org/2000/svg">
    <defs>
      <clipPath id="shape-500">
        <path d="M0,95 Q0,32 55,22 Q302,-22 550,22 Q605,32 605,95 V1155 Q605,1200 560,1200 H45 Q0,1200 0,1155 Z"/>
      </clipPath>
      <linearGradient id="head-500" x1="0" y1="0" x2="0" y2="1">
        <stop offset="0" stop-color="var(--navy)"/>
        <stop offset="0.5" stop-color="var(--mid-blue)"/>
        <stop offset="1" stop-color="var(--sky-blue)"/>
      </linearGradient>
      <linearGradient id="foot-500" x1="0" y1="0" x2="0" y2="1">
        <stop offset="0" stop-color="var(--mid-blue)"/>
        <stop offset="0.55" stop-color="var(--navy)"/>
        <stop offset="1" stop-color="var(--navy-deep)"/>
      </linearGradient>
      <linearGradient id="photo-500" x1="0" y1="0" x2="1" y2="0">
        <stop offset="0" stop-color="#8d8b88"/>
        <stop offset="0.4" stop-color="#c9c7c4"/>
        <stop offset="0.7" stop-color="#e9e9e9"/>
        <stop offset="1" stop-color="#b5b3b0"/>
      </linearGradient>
      <g id="tick-500">
        <circle class="tick-ring" r="17" stroke-width="2.6"/>
        <path class="tick-mark" d="M-8,0 L-2,8 L12,-14" stroke-width="3"/>
      </g>
    </defs>
    <g clip-path="url(#shape-500)">
      <rect width="605" height="1200" fill="var(--white)"/>
      <rect y="230" width="605" height="312" fill="url(#head-500)"/>
      <rect y="540" width="605" height="363" fill="url(#photo-500)" role="img" aria-label="Photo of a modern tiled bathroom with walk-in shower, washbasin and bathtub"/>
      <rect y="903" width="605" height="297" fill="url(#foot-500)"/>
    </g>
    <path d="M0,95 Q0,32 55,22 Q302,-22 550,22 Q605,32 605,95 V1155 Q605,1200 560,1200 H45 Q0,1200 0,1155 Z" fill="none" stroke="var(--outline)" stroke-width="3"/>

    <circle cx="302" cy="88" r="52" fill="var(--brand-blue)"/>
    <text class="wordmark" x="302" y="190" font-size="54" text-anchor="middle">vorlix</text>

    <text class="title" x="302" y="325" font-size="72" text-anchor="middle">SANITARY</text>
    <text class="title" x="302" y="395" font-size="74" text-anchor="middle" letter-spacing="28">CLEANER</text>
    <text class="tagline" x="302" y="458" font-size="30" text-anchor="middle">CLEANS, DESCALES &amp; FRESHENS</text>

    <circle cx="449" cy="592" r="101" fill="var(--badge)"/>
    <text class="badge-text" x="449" y="551" font-size="28" text-anchor="middle">Ideal For</text>
    <text class="badge-text" x="449" y="583" font-size="28" text-anchor="middle">Quick and</text>
    <text class="badge-text" x="449" y="615" font-size="28" text-anchor="middle">Powerful</text>
    <text class="badge-text" x="449" y="647" font-size="28" text-anchor="middle">Cleaning</text>

    <use href="#tick-500" x="64" y="971"/>
    <text class="usp" x="88" y="987" font-size="44">Sanitary</text>
    <use href="#tick-500" x="320" y="971"/>
    <text class="usp" x="344" y="987" font-size="44">Bathroom</text>
    <use href="#tick-500" x="94" y="1034"/>
    <text class="usp" x="118" y="1050" font-size="44">Toilet</text>
    <use href="#tick-500" x="282" y="1034"/>
    <text class="usp" x="306" y="1050" font-size="44">Wet Areas</text>

    <text class="usage" x="302" y="1122" font-size="19" text-anchor="middle" letter-spacing="1.5">A READY-TO-USE PRODUCT FOR EVERYDAY USE</text>
    <text class="volume" x="302" y="1171" font-size="32" text-anchor="middle">500 ml</text>
  </svg>

  <!-- 1 litre label -->
  <svg class="label label--1000" viewBox="0 0 763 1461" xmlns="http://www.w3.org/2000/svg">
    <defs>
      <clipPath id="shape-1000">
        <path d="M0,110 Q0,40 68,27 Q381,-28 694,27 Q763,40 763,110 V1400 Q763,1461 702,1461 H61 Q0,1461 0,1400 Z"/>
      </clipPath>
      <linearGradient id="head-1000" x1="0" y1="0" x2="0" y2="1">
        <stop offset="0" stop-color="var(--navy)"/>
        <stop offset="0.5" stop-color="var(--mid-blue)"/>
        <stop offset="1" stop-color="var(--sky-blue)"/>
      </linearGradient>
      <linearGradient id="foot-1000" x1="0" y1="0" x2="0" y2="1">
        <stop offset="0" stop-color="var(--mid-blue)"/>
        <stop offset="0.55" stop-color="var(--navy)"/>
        <stop offset="1" stop-color="var(--navy-deep)"/>
      </linearGradient>
      <linearGradient id="photo-1000" x1="0" y1="0" x2="1" y2="0">
        <stop offset="0" stop-color="#8d8b88"/>
        <stop offset="0.4" stop-color="#c9c7c4"/>
        <stop offset="0.7" stop-color="#e9e9e9"/>
        <stop offset="1" stop-color="#b5b3b0"/>
      </linearGradient>
      <g id="tick-1000">
        <circle class="tick-ring" r="22" stroke-width="3.2"/>
        <path class="tick-mark" d="M-10,0 L-3,10 L15,-18" stroke-width="3.8"/>
      </g>
    </defs>
    <g clip-path="url(#shape-1000)">
      <rect width="763" height="1461" fill="var(--white)"/>
      <rect y="263" width="763" height="395" fill="url(#head-1000)"/>
      <rect y="656" width="763" height="430" fill="url(#photo-1000)" role="img" aria-label="Photo of a modern tiled bathroom with walk-in shower, washbasin and bathtub"/>
      <rect y="1086" width="763" height="375" fill="url(#foot-1000)"/>
    </g>
    <path d="M0,110 Q0,40 68,27 Q381,-28 694,27 Q763,40 763,110 V1400 Q763,1461 702,1461 H61 Q0,1461 0,1400 Z" fill="none" stroke="var(--outline)" stroke-width="3"/>

    <circle cx="381" cy="111" r="66" fill="var(--brand-blue)"/>
    <text class="wordmark" x="381" y="240" font-size="68" text-anchor="middle">vorlix</text>

    <text class="title" x="381" y="383" font-size="94" text-anchor="middle">SANITARY</text>
    <text class="title" x="381" y="471" font-size="96" text-anchor="middle" letter-spacing="36">CLEANER</text>
    <text class="tagline" x="381" y="553" font-size="38" text-anchor="middle">CLEANS, DESCALES &amp; FRESHENS</text>

    <circle cx="565" cy="721" r="128" fill="var(--badge)"/>
    <text class="badge-text" x="565" y="669" font-size="36" text-anchor="middle">Ideal For</text>
    <text class="badge-text" x="565" y="709" font-size="36" text-anchor="middle">Quick and</text>
    <text class="badge-text" x="565" y="749" font-size="36" text-anchor="middle">Powerful</text>
    <text class="badge-text" x="565" y="789" font-size="36" text-anchor="middle">Cleaning</text>

    <use href="#tick-1000" x="80" y="1172"/>
    <text class="usp" x="110" y="1193" font-size="58">Sanitary</text>
    <use href="#tick-1000" x="402" y="1172"/>
    <text class="usp" x="434" y="1193" font-size="58">Bathroom</text>
    <use href="#tick-1000" x="119" y="1252"/>
    <text class="usp" x="150" y="1273" font-size="58">Toilet</text>
    <use href="#tick-1000" x="356" y="1252"/>
    <text class="usp" x="388" y="1273" font-size="58">Wet Areas</text>

    <text class="usage" x="381" y="1361" font-size="25" text-anchor="middle" letter-spacing="2">A READY-TO-USE PRODUCT FOR EVERYDAY USE</text>
    <text class="volume" x="381" y="1423" font-size="40" text-anchor="middle">1 Lt</text>
  </svg>

</div>
</body>
</html>
```